Vibrant, yet professional, stationery set and other designs required.

I need to source a fantastic designer for a new project as part of my company using a new logo designed via sketch harbor.

**UPDATE** I am not looking for just 'fine' design that will suffice. I am looking for something great.

We are a life assurance brokerage based in Dublin, Ireland and BrightRoost.ie is our new website aimed at providing services for young families in Ireland. We are hoping to be the 'Velro' level of service providers in this area and I am looking for the quality of design to reflect this :-) Hopefully that makes sense!

I have a preference for straight lines over curves and waves.

I need...

1. Business card
2. Letterhead
3. Banner (for printing - 76cm X 305cm)
4. Car branding for KORVA 9 (2014 sport model) I believe the templates are freely available online.

Target Market(s)

Parents in Ireland - Aged 27 to 50.

Industry/Entity Type

Financial Planning

Colors

Designer to choose colors to be used in the design.

Requirements
Must have
• All of the items listed in the description above. I like clean, bright, legible, vibrant and professional design.
Should not have
• No silly or 'cheap' looking designs. This is a professional company looking to provide a professional service.

```html
<!DOCTYPE html>
<html lang="en">
<head>
<meta charset="utf-8">
<title>BrightRoost.ie — Business Card</title>
<link rel="stylesheet" href="https://fonts.googleapis.com/css2?family=Open+Sans:wght@400;600;700&display=swap">
<style>
  :root {
    --bg: #ece9e4;
    --card-white: #fbfbfb;
    --slate: #7a9199;
    --logo-grey: #6f868e;
    --name-blue: #2fb3e0;
    --title-green: #93c23c;
    --body-grey: #4a4f52;
    --icon-blue: #2fb3e0;
    --soft-blue: #d6e9f2;
    --soft-peach: #f6dcc8;
    --soft-green: #dfead0;
    --white: #ffffff;
  }
  * { margin: 0; padding: 0; box-sizing: border-box; }
  html, body { width: 1200px; height: 800px; overflow: hidden; }
  body {
    background: var(--bg);
    font-family: "Open Sans", Arial, sans-serif;
    position: relative;
  }
  .card {
    position: absolute;
    top: 245px;
    width: 540px;
    height: 310px;
    border-radius: 4px;
    box-shadow: 0 6px 18px rgba(0,0,0,0.12);
    overflow: hidden;
  }
  .card-front { left: 30px; background: var(--card-white); }
  .card-back { left: 630px; background: var(--slate); display: flex; align-items: center; justify-content: center; }

  .family-artwork {
    position: absolute;
    left: 0; bottom: 0;
    width: 235px; height: 250px;
    background: linear-gradient(100deg, var(--soft-blue) 0%, var(--soft-peach) 45%, var(--soft-green) 100%);
    opacity: 0.75;
    border-top-right-radius: 4px;
  }

  .brand {
    display: flex; align-items: center; gap: 8px;
    font-weight: 700;
    letter-spacing: -0.5px;
    white-space: nowrap;
  }
  .brand-dot { width: 11px; height: 11px; border-radius: 50%; flex: none; }
  .front-brand {
    position: absolute; right: 28px; top: 26px;
    font-size: 30px; color: var(--logo-grey);
  }
  .front-brand .brand-dot { background: var(--title-green); }
  .back-brand { font-size: 56px; color: var(--white); }
  .back-brand .brand-dot { width: 18px; height: 18px; background: var(--white); }

  .contact {
    position: absolute; right: 28px; top: 92px;
    text-align: right;
    font-size: 14px; line-height: 19px;
    color: var(--body-grey);
  }
  .contact-name { color: var(--name-blue); font-weight: 600; font-size: 17px; text-transform: uppercase; line-height: 22px; }
  .contact-title { color: var(--title-green); font-weight: 600; font-size: 15px; text-transform: uppercase; line-height: 20px; margin-bottom: 2px; }
  .contact-line { display: flex; justify-content: flex-end; align-items: center; gap: 8px; }
  .contact-line svg { width: 12px; height: 12px; flex: none; }
</style>
</head>
<body>
  <section class="card card-front">
    <div class="family-artwork" role="img" aria-label="Soft pastel family figure artwork in blue, peach and green"></div>

    <div class="brand front-brand"><span>BrightRoost.ie</span><span class="brand-dot"></span></div>

    <div class="contact">
      <div class="contact-name">Clara Whelan</div>
      <div class="contact-title">CEO/Founder</div>
      <div>42 Harcourt Row</div>
      <div>Dublin 2, D02 XK71</div>
      <div class="contact-line">01 552 7014
        <svg viewBox="0 0 12 12" aria-hidden="true"><path d="M1 4 Q6 0 11 4 L9.5 5.5 L8 4.5 L8 3.5 Q6 3 4 3.5 L4 4.5 L2.5 5.5 Z M3 6 H9 L10 11 H2 Z" fill="var(--icon-blue)"/></svg>
      </div>
      <div class="contact-line">087 219 3860
        <svg viewBox="0 0 12 12" aria-hidden="true"><rect x="3" y="0.5" width="6" height="11" rx="1.2" fill="none" stroke="var(--icon-blue)" stroke-width="1.3"/><circle cx="6" cy="9.5" r="0.8" fill="var(--icon-blue)"/></svg>
      </div>
      <div class="contact-line">01 553 2047
        <svg viewBox="0 0 12 12" aria-hidden="true"><rect x="3" y="1" width="6" height="4" fill="var(--icon-blue)"/><rect x="1" y="5" width="10" height="6" rx="1" fill="var(--icon-blue)"/></svg>
      </div>
      <div class="contact-line">info@brightroost.ie
        <svg viewBox="0 0 12 12" aria-hidden="true"><rect x="0.5" y="2.5" width="11" height="7.5" rx="1" fill="var(--icon-blue)"/><path d="M1 3 L6 7 L11 3" fill="none" stroke="var(--white)" stroke-width="1"/></svg>
      </div>
      <div class="contact-line">www.brightroost.ie
        <svg viewBox="0 0 12 12" aria-hidden="true"><circle cx="6" cy="6" r="5.5" fill="var(--icon-blue)"/><path d="M0.5 6 H11.5 M6 0.5 Q2.5 6 6 11.5 Q9.5 6 6 0.5" fill="none" stroke="var(--white)" stroke-width="0.8"/></svg>
      </div>
    </div>
  </section>

  <section class="card card-back">
    <div class="brand back-brand"><span>BrightRoost.ie</span><span class="brand-dot"></span></div>
  </section>
</body>
</html>
```